Satchel & Sundial needs new business card design

I need a new business card design. I'm looking for out-of-the-box design which represents the freedom of being a location independent entrepreneur.
I offer coaching, retreats and trips.
I would like to see designs with and without the photo.
Colors I use are black (#000000), green (#25A796) and brown (#D7C38C)
Website satchelandsundial.example

Target Market(s)

location independent entrepreneurs, digital nomads, people looking to swap the 9 to 5 for a lifestyle business

Industry/Entity Type

Business

Contact Information for Business Card

Dorota Falkner
Your Lifestyle Business Coach, Retreat & Trip Leader
http://satchelandsundial.example
hello@satchelandsundial.example
Live a life you don't need a holiday from

Font styles to use
Serif
Sans Serif

Requirements
Must have
• One side should contain only the logo. I would also consider having the "Live a life you don't need a holiday from" on that side too (depending on how it looks)
• Please show both sides on the designs.

```html
<!DOCTYPE html>
<html lang="en">
<head>
<meta charset="utf-8">
<title>Satchel &amp; Sundial — Business Card</title>
<link rel="stylesheet" href="https://fonts.googleapis.com/css2?family=Oswald:wght@400;500&display=swap">
<style>
  :root {
    --ink: #000000;
    --teal: #25A796;
    --teal-band: #138a78;
    --sand: #D7C38C;
    --charcoal: #1e2022;
    --paper: #f4f4f4;
    --stage: #e4e4e4;
    --white: #ffffff;
  }
  * { box-sizing: border-box; margin: 0; padding: 0; }
  html, body { width: 1200px; height: 576px; overflow: hidden; }
  body {
    background: var(--stage);
    font-family: "Oswald", "Arial Narrow", sans-serif;
    position: relative;
  }
  .card {
    position: absolute;
    top: 138px;
    width: 484px;
    height: 292px;
    border-radius: 6px;
    overflow: hidden;
    box-shadow: 0 3px 6px rgba(0,0,0,0.25);
  }
  .card-front {
    left: 82px;
    background: linear-gradient(180deg, #fbfbfb 0%, #ececec 100%);
  }
  .card-back {
    left: 602px;
    width: 480px;
    height: 290px;
    background: var(--charcoal);
  }
  .url-band {
    position: absolute;
    left: 0; right: 0; bottom: 0;
    height: 34px;
    background: var(--teal-band);
    color: var(--white);
    font-size: 13px;
    display: flex;
    align-items: center;
    justify-content: center;
    letter-spacing: 0.2px;
  }
  .brand-name {
    position: absolute;
    top: 100px;
    left: 0; right: 0;
    text-align: center;
    font-size: 42px;
    font-weight: 500;
    color: var(--ink);
    text-transform: uppercase;
    letter-spacing: 1px;
  }
  .portrait {
    position: absolute;
    top: 0; left: 0;
  }
  .identity {
    position: absolute;
    left: 28px;
    top: 36px;
  }
  .person-name {
    color: var(--sand);
    font-size: 21px;
    font-weight: 500;
    text-transform: uppercase;
    line-height: 1.2;
  }
  .person-role {
    color: var(--white);
    font-size: 12px;
    line-height: 1.45;
    margin-top: 2px;
  }
  .contact-list {
    position: absolute;
    left: 28px;
    top: 151px;
    list-style: none;
    color: var(--white);
    font-size: 13px;
  }
  .contact-list li {
    display: flex;
    align-items: center;
    height: 20px;
  }
  .contact-icon {
    width: 12px; height: 10px;
    margin-right: 7px;
  }
  .social-mark {
    width: 10px; height: 10px;
    background: var(--teal);
    border-radius: 2px;
    margin-right: 7px;
  }
  .tagline {
    position: absolute;
    left: 28px;
    top: 222px;
    color: var(--teal);
    font-size: 14px;
  }
</style>
</head>
<body>

  <section class="card card-front" aria-label="Card front">
    <div class="brand-name">Satchel &amp; Sundial</div>
    <div class="url-band">www.satchelandsundial.example</div>
  </section>

  <section class="card card-back" aria-label="Card back">
    <svg class="portrait" width="480" height="258" viewBox="0 0 480 258">
      <defs>
        <linearGradient id="foliage" x1="0" y1="0" x2="1" y2="1">
          <stop offset="0" stop-color="#6f7f5a"/>
          <stop offset="0.5" stop-color="#9aa784"/>
          <stop offset="1" stop-color="#5f6b4c"/>
        </linearGradient>
      </defs>
      <path d="M 262 0 Q 244 120 268 258 L 263 258 Q 236 125 255 0 Z" fill="var(--teal)"/>
      <path d="M 270 0 Q 250 120 274 258 L 480 258 L 480 0 Z"
            fill="url(#foliage)" role="img"
            aria-label="Photo of the coach seated outdoors among trees, holding a small sign"/>
    </svg>

    <div class="identity">
      <h1 class="person-name">Dorota Falkner</h1>
      <p class="person-role">Your Lifestyle Business Coach<br>Retreat &amp; Trip Leader</p>
    </div>

    <ul class="contact-list">
      <li>
        <svg class="contact-icon" viewBox="0 0 12 10" aria-hidden="true">
          <rect x="0.5" y="0.5" width="11" height="9" fill="var(--teal)"/>
          <path d="M0.5 0.5 L6 5.5 L11.5 0.5" fill="none" stroke="var(--charcoal)" stroke-width="1.2"/>
        </svg>
        hello@satchelandsundial.example
      </li>
      <li><span class="social-mark" aria-hidden="true"></span>/satchelandsundial</li>
    </ul>

    <p class="tagline">Live a life you don't need a holiday from</p>

    <div class="url-band">www.satchelandsundial.example</div>
  </section>

</body>
</html>
```